One page flyer for nonprofit focused IT company

I need a one page flyer (one side of a single 8.5x11 page) with text and graphics. The company logo is already done, and it must appear on the flyer along with other icons and graphics. The final design will be printed on heavy weight glossy paper as a handout and also distributed as a PDF.

The text is provided in an attachment, if it needs to be shortened let me know.

Industry/Entity Type

Information Technology

Requirements
Must have
• some flare (colors, icons or images)
Should not have
• While we work for nonprofits, my company is a FOR PROFIT company.

```html
<!DOCTYPE html>
<html lang="en">
<head>
<meta charset="utf-8">
<title>Keystone Systems Corporation – Flyer</title>
<link rel="stylesheet" href="https://fonts.googleapis.com/css2?family=Montserrat:wght@700;800;900&family=Roboto:wght@400;700&display=swap">
<style>
:root{
  --red:#9b1b2c;
  --red-dark:#7d1322;
  --ink:#222;
  --charcoal:#3a3a3a;
  --paper:#ffffff;
  --backdrop:#d9d9d9;
  --sky-deep:#0a2a66;
  --sky-mid:#1d5fb4;
  --sky-glow:#6fb6f0;
}
*{margin:0;padding:0;box-sizing:border-box}
html,body{width:1200px;height:2760px;overflow:hidden;background:var(--backdrop)}
.flyer{
  position:absolute;left:93px;top:724px;width:947px;height:1225px;
  transform:scale(1.0708);transform-origin:0 0;
  background:var(--paper);overflow:hidden;
  box-shadow:0 10px 30px rgba(0,0,0,.25);
  font-family:'Roboto',sans-serif;color:var(--ink);
}
.header-art{position:absolute;left:0;top:0;width:947px;height:440px}
.brand{
  position:absolute;left:100px;top:78px;width:360px;text-align:center;
  font-family:'Montserrat',sans-serif;font-weight:700;color:var(--red);
  font-size:30px;letter-spacing:1px;line-height:1.1;
}
.brand-square{display:inline-block;width:34px;height:34px;background:var(--red);vertical-align:-4px;margin-right:10px}
.brand-sub{display:block;font-size:14px;letter-spacing:9px;margin-top:6px}
.headline{
  position:absolute;left:38px;top:196px;color:#fff;
  font-family:'Montserrat',sans-serif;font-weight:900;line-height:1;
}
.headline .l1{display:block;font-size:62px;letter-spacing:1px}
.headline .l2{display:block;font-size:41px;margin-top:4px}
.column{
  position:absolute;display:flex;flex-direction:column;justify-content:space-between;
}
.col-left{left:60px;top:428px;height:692px;width:392px}
.col-right{left:498px;top:436px;height:660px;width:384px}
.item{width:100%}
.item-head{display:flex;align-items:center;gap:14px;margin-bottom:10px}
.icon{flex:0 0 40px;width:40px;height:40px}
.item-title{font-family:'Montserrat',sans-serif;font-weight:700;color:var(--red);font-size:15.5px;line-height:1.15}
.item-text{font-size:15.6px;line-height:18.6px;text-align:justify}
.item-text b{font-weight:700}
.footer{
  position:absolute;left:0;top:1153px;width:947px;height:72px;background:var(--red);
  display:flex;align-items:center;justify-content:space-between;padding:0 66px 0 70px;
  color:#fff;font-family:'Montserrat',sans-serif;font-weight:700;font-size:15px;
}
.contact{display:flex;align-items:center;gap:9px}
.contact svg{width:20px;height:20px}
</style>
</head>
<body>
<main class="flyer">
  <svg class="header-art" viewBox="0 0 947 440">
    <defs>
      <radialGradient id="skyFill" cx="0.55" cy="0.35" r="0.75">
        <stop offset="0" stop-color="#6fb6f0"/>
        <stop offset="0.45" stop-color="#1d5fb4"/>
        <stop offset="1" stop-color="#0a2a66"/>
      </radialGradient>
      <clipPath id="photoClip"><circle cx="835" cy="110" r="292"/></clipPath>
    </defs>
    <path class="band-shadow" d="M0 432 C160 360 330 330 520 338 L520 350 C330 345 170 375 0 448 Z" fill="#3a3a3a"/>
    <path class="band-red" d="M0 165 H947 V300 C760 330 620 312 520 318 C330 330 160 360 0 420 Z" fill="#9b1b2c"/>
    <circle cx="835" cy="110" r="312" fill="none" stroke="#9b1b2c" stroke-width="6"/>
    <circle cx="835" cy="110" r="302" fill="#fff"/>
    <rect x="500" y="0" width="447" height="410" fill="url(#skyFill)" clip-path="url(#photoClip)" role="img" aria-label="Photo of a hand holding a tablet with a glowing cloud upload symbol above a city skyline"/>
  </svg>

  <div class="brand"><span class="brand-square"></span>Keystone Systems<span class="brand-sub">CORPORATION</span></div>

  <h1 class="headline"><span class="l1">50 YEARS OF</span><span class="l2">NONPROFIT IT SERVICES</span></h1>

  <section class="column col-left">
    <article class="item">
      <div class="item-head"><svg class="icon" viewBox="0 0 40 40"><circle cx="20" cy="20" r="18" fill="none" stroke="var(--charcoal)" stroke-width="1.5"/><circle cx="20" cy="20" r="6" fill="none" stroke="var(--red)" stroke-width="2"/><path d="M20 9v5M20 26v5M9 20h5M26 20h5" stroke="var(--red)" stroke-width="2"/></svg><h2 class="item-title">An Efficient and Elegant Approach to IT Solution Implementations</h2></div>
      <p class="item-text">Keystone Systems Corporation has been supporting the Information Systems needs of nonprofits for over 50 years. We continually strive to bring the latest technologies and best practices to nonprofits to drive down the cost of IT while implementing systems that drive revenue. Our Agile approach to IT management means that we deliver working systems to every one of our clients every two weeks.</p>
    </article>
    <article class="item">
      <div class="item-head"><svg class="icon" viewBox="0 0 40 40"><circle cx="20" cy="20" r="18" fill="none" stroke="var(--charcoal)" stroke-width="1.5"/><path d="M12 28V18h5v10M18 28V12h5v16M24 28V20h5v8" fill="none" stroke="var(--red)" stroke-width="2"/></svg><h2 class="item-title">Successes 90% Reduction in Software Development Costs</h2></div>
      <p class="item-text">Harlow’s National Auto Retailers Guild needed to update their core product offering; they engaged their in-house IT department who estimated the project would take 3 years at a cost of $3,000,000. NARG decided to work with Keystone Systems Corporation instead, and the product was released to production in only 9 months at <b>one tenth of the cost</b>, only $300,000</p>
    </article>
    <article class="item">
      <div class="item-head"><svg class="icon" viewBox="0 0 40 40"><circle cx="20" cy="20" r="18" fill="none" stroke="var(--charcoal)" stroke-width="1.5"/><rect x="12" y="14" width="16" height="13" fill="none" stroke="var(--red)" stroke-width="2"/><path d="M15 19h10M15 23h7" stroke="var(--red)" stroke-width="1.6"/></svg><h2 class="item-title">10x Increase in Membership</h2></div>
      <p class="item-text">Greenway Paths Conservancy needed to move to online membership registration and contracted with Keystone Systems Corporation to build a significant online presence and engage potential members. Through compelling online tools and mobile applications Greenway Paths has <b>increased membership 10 fold.</b></p>
    </article>
    <article class="item">
      <div class="item-head"><svg class="icon" viewBox="0 0 40 40"><circle cx="20" cy="20" r="18" fill="none" stroke="var(--charcoal)" stroke-width="1.5"/><ellipse cx="20" cy="13" rx="8" ry="3" fill="none" stroke="var(--red)" stroke-width="2"/><path d="M12 13v14c0 4 16 4 16 0V13M12 20c0 4 16 4 16 0" fill="none" stroke="var(--red)" stroke-width="2"/></svg><h2 class="item-title">Member Donor Database</h2></div>
      <p class="item-text">Keystone Systems Corporation’s GiveLedger Member / Donor CRM system is fully customized for each client meeting the unique needs of your organization.</p>
    </article>
  </section>

  <section class="column col-right">
    <article class="item">
      <div class="item-head"><svg class="icon" viewBox="0 0 40 40"><circle cx="20" cy="20" r="18" fill="none" stroke="var(--charcoal)" stroke-width="1.5"/><path d="M20 10v16M14 21l6 6 6-6" fill="none" stroke="var(--red)" stroke-width="2"/></svg><h2 class="item-title">20% Reduction in Overhead</h2></div>
      <p class="item-text">The National Women's Alliance had antiquated systems and processes in place to manage over 500 chapters across the nation. Working with KSC they implemented online tools to allow communication and management between the local chapters and national headquarters. This eliminated much of the overhead of chapter management, <b>reducing HR costs by 20%.</b></p>
    </article>
    <article class="item">
      <div class="item-head"><svg class="icon" viewBox="0 0 40 40"><circle cx="20" cy="20" r="18" fill="none" stroke="var(--charcoal)" stroke-width="1.5"/><rect x="14" y="10" width="12" height="20" rx="2" fill="none" stroke="var(--red)" stroke-width="2"/><circle cx="20" cy="26" r="1.3" fill="var(--red)"/></svg><h2 class="item-title">Mobile Applications</h2></div>
      <p class="item-text">Keystone Systems Corporation implements mobile applications for phones and tablets to provide direct communications with members and donors enabling real-time, two way interaction.</p>
    </article>
    <article class="item">
      <div class="item-head"><svg class="icon" viewBox="0 0 40 40"><circle cx="20" cy="20" r="18" fill="none" stroke="var(--charcoal)" stroke-width="1.5"/><circle cx="14" cy="15" r="3.5" fill="none" stroke="var(--red)" stroke-width="2"/><circle cx="26" cy="15" r="3.5" fill="none" stroke="var(--red)" stroke-width="2"/><circle cx="20" cy="26" r="3.5" fill="none" stroke="var(--red)" stroke-width="2"/><path d="M16 17l3 6M24 17l-3 6" stroke="var(--red)" stroke-width="1.6"/></svg><h2 class="item-title">Systems Integration</h2></div>
      <p class="item-text">Every nonprofit’s IT applications are scattered and disconnected. Keystone System Corporation has decades of experience integrating these applications into a single cohesive system.</p>
    </article>
    <article class="item">
      <div class="item-head"><svg class="icon" viewBox="0 0 40 40"><circle cx="20" cy="20" r="18" fill="none" stroke="var(--charcoal)" stroke-width="1.5"/><rect x="12" y="11" width="16" height="18" fill="none" stroke="var(--red)" stroke-width="2"/><path d="M16 25v-4M20 25v-8M24 25v-6" stroke="var(--red)" stroke-width="2"/></svg><h2 class="item-title">Business Intelligence and Reporting</h2></div>
      <p class="item-text">Keystone Systems Corporation can wrestle all of an organization's data into simple executive dashboards and reports.</p>
    </article>
    <article class="item">
      <div class="item-head"><svg class="icon" viewBox="0 0 40 40"><circle cx="20" cy="20" r="18" fill="none" stroke="var(--charcoal)" stroke-width="1.5"/><path d="M13 24a4 4 0 0 1 1-8 6 6 0 0 1 11-1 4.5 4.5 0 0 1 2 9Z" fill="none" stroke="var(--red)" stroke-width="2"/><path d="M20 20v10M17 27l3 3 3-3" fill="none" stroke="var(--red)" stroke-width="1.6"/></svg><h2 class="item-title">Cloud Migration</h2></div>
      <p class="item-text">Reduce IT costs by migrating to the latest cloud solutions.</p>
    </article>
  </section>

  <footer class="footer">
    <span class="contact"><svg viewBox="0 0 20 20"><circle cx="10" cy="10" r="9" fill="none" stroke="#fff" stroke-width="1.3"/><path d="M7 5.5l2 2-1 1.5a6 6 0 0 0 3 3l1.5-1 2 2-1.5 1.5C9 14 6 11 5.5 7Z" fill="#fff"/></svg>555-014-2368</span>
    <span class="contact"><svg viewBox="0 0 20 20"><circle cx="10" cy="10" r="9" fill="none" stroke="#fff" stroke-width="1.3"/><rect x="5.5" y="7" width="9" height="6.5" fill="none" stroke="#fff" stroke-width="1.2"/><path d="M5.5 7l4.5 3.5L14.5 7" fill="none" stroke="#fff" stroke-width="1.2"/></svg>info@keystonesystems.com</span>
    <span class="contact"><svg viewBox="0 0 20 20"><circle cx="10" cy="10" r="9" fill="none" stroke="#fff" stroke-width="1.3"/><circle cx="10" cy="10" r="5.5" fill="none" stroke="#fff" stroke-width="1.1"/><path d="M4.5 10h11M10 4.5c-3 3-3 8 0 11M10 4.5c3 3 3 8 0 11" fill="none" stroke="#fff" stroke-width="1"/></svg>www.keystonesystems.com</span>
  </footer>
</main>
</body>
</html>
```